Design Website to Recruit next Generation of Steel Harbor's Order Vantage

Design a cool website that provides just enough information to be intriguing to teenagers who compete in combat sports. The format is to make this an invite-only team of high-school-aged competitors in combat sports (predominately Jiu Jitsu right now). Cinder Ravens can participate in similar assignments to earn consideration. We are modeled after the Order Vantage formed in Steel Harbor and would like to keep that look and feel. The document attached "OV - Ideas and Content for Website" shows our initial thoughts and here is more about us:

Goal - To promote the success of committed teenage Jiu Jitsu competitors who excel through focused preparation and deliberate practice.

Why - Prove the core principles of success.

How - Success is its own reward and always entails an element of the unknown/uncontrollable. We reward preparation. Setting clear goals (SMART), deliberate practice, building mental models (domain specific knowledge), restorative recovery, nutritional coaching, power of teaching others, sports science (strength & conditioning), expert guidance, personalized development plans, accountability, Quantified Self, gamification and competitive challenges. What - We will win at the highest of levels across the fight world by applying the general principles of success. These lessons will be carried with them to other areas of their lives.

Our primary goal with the website would be to share our company’s mission statement and promote the success of our sponsored athletes.

The only social media account we have currently is Pixtrelle's @ordervantageK7 (recently established). If you want more of an idea for what our online presence should feel like, then I would suggest watching these two scenes from Steel Harbor:

Recruiting: This scene shows the process for joining Order Vantage: https://vidrelo.net/Qk82LmTrA

Order Vantage Assignments: This shows how assignments are handed out for members to accomplish: https://vidrelo.net/Zp41XwNeB

Order Vantage Color Assignment: This is their first large assignment and where the green color comes from: https://vidrelo.net/Hd67VcJuC

It is also worth noting that "less is more" considering the first rule is, "you do not talk about..." That should carry over to our website and social media presence. We want to share just enough to be intriguing to inquiring minds and motivational for members, but no more.

I have uploaded a bunch of content, but just wanted to give you a broader idea. Feel free to design as you see fit...
Updates

Please stay tuned for the "burning smiley face" files. I have purchased a rendering of it so we have a proprietary vector image to use on our site. There will also be files for different versions of the Order Vantage//OV logos for various subcategories. Here is how they are to be applied: Circled = Primary (for main/landing page), Jiu Jitsu = Pyramid, Wrestling = Traditional, Muay Thai = Rolled, and Legacy OV = Original (coming soon).

Target Market(s)

Teenage competitors of combat sports, their parents, and sponsors of those athletes

Industry/Entity Type

Martial Arts & High School Sports

Coding

Coded - Design and coding required

Number of Pages Required

5+ page

Font styles to use
Sans Serif
Other font styles liked:
• See font in "Circled Logo"

Colors
59FF00
82FF00
B8FF75
E3FFCB
F4FFEA
EB3D1F
EC4F4E
F09395
F8D3D4
FCEDEE

Requirements
Must have
• Cool landing page with logo and brief summary of what we do. Page with 8 rules and explanation for earning an invitation. Plus, accomplishments page for memorializing the success of sponsored "Cinder Ravens"
Should not have
• Individual names

```html
<!DOCTYPE html>
<html lang="en">
<head>
<meta charset="utf-8">
<title>Order Vantage — Invite Only</title>
<link rel="stylesheet" href="https://fonts.googleapis.com/css2?family=Kanit:ital,wght@0,500;0,600;0,700;1,600;1,700&family=Lato:wght@400;700&display=swap">
<style>
  :root {
    --green: #3f9547;
    --green-bright: #59c64a;
    --red: #8f281f;
    --red-button: #a3312a;
    --red-text: #c0392b;
    --charcoal: #3a3a3a;
    --charcoal-deep: #333333;
    --black: #000000;
    --white: #ffffff;
    --ink: #111111;
    --hero-dark: #1e1c1b;
    --hero-mid: #4a4440;
  }
  * { margin: 0; padding: 0; box-sizing: border-box; }
  html, body { width: 1200px; height: 3668px; overflow: hidden; background: var(--white); }
  body { font-family: "Lato", Arial, sans-serif; color: var(--ink); }
  .page { position: relative; width: 1200px; height: 3668px; overflow: hidden; }
  .display { font-family: "Kanit", "Arial Narrow", sans-serif; text-transform: uppercase; }

  /* Hero */
  .hero { position: absolute; left: 0; top: 0; width: 1200px; height: 624px; }
  .hero-scene { position: absolute; inset: 0; background: radial-gradient(ellipse at 60% 45%, #6d6660 0%, var(--hero-mid) 35%, var(--hero-dark) 85%); }
  .brand { position: absolute; left: 111px; top: 90px; font-family: "Kanit", sans-serif; font-weight: 600; font-size: 19px; color: var(--green-bright); letter-spacing: 0.5px; }
  .menu { position: absolute; left: 1015px; top: 57px; color: var(--white); font-family: "Kanit", sans-serif; font-weight: 600; font-size: 16px; display: flex; align-items: center; gap: 8px; }
  .menu-icon { width: 14px; height: 12px; border-top: 2px solid var(--white); border-bottom: 2px solid var(--white); position: relative; }
  .menu-icon::after { content: ""; position: absolute; left: 0; right: 0; top: 3px; border-top: 2px solid var(--white); }
  .hero-title { position: absolute; left: 0; width: 1200px; top: 240px; text-align: center; color: var(--white); font-weight: 700; font-style: italic; font-size: 45px; line-height: 52px; }
  .btn { display: inline-flex; align-items: center; justify-content: center; background: var(--red-button); color: var(--white); font-family: "Kanit", sans-serif; font-weight: 600; text-transform: uppercase; border-radius: 4px; }
  .hero-btn { position: absolute; left: 517px; top: 421px; width: 166px; height: 57px; font-size: 17px; }

  /* Intro */
  .intro { position: absolute; left: 0; top: 624px; width: 1200px; height: 468px; background: var(--charcoal); overflow: hidden; }
  .intro-curve { position: absolute; inset: 0; }
  .intro-title { position: absolute; left: 112px; top: 80px; color: var(--white); font-size: 35px; font-weight: 700; }
  .intro-sub { position: absolute; left: 112px; top: 137px; color: var(--red-text); font-size: 19px; font-weight: 600; }
  .intro-text { position: absolute; left: 112px; top: 192px; width: 470px; color: var(--white); font-size: 17px; line-height: 28px; }
  .intro-motto { position: absolute; left: 112px; top: 318px; color: var(--green-bright); font-size: 17px; font-weight: 600; }
  .intro-portrait { position: absolute; left: 731px; top: 39px; width: 326px; height: 326px; border-radius: 50%; background: radial-gradient(circle at 50% 40%, #3f5f5a 0%, #1a2322 60%, #0d0d0d 100%); }

  /* Principles */
  .principles { position: absolute; left: 0; top: 1092px; width: 1200px; height: 965px; background: var(--white); }
  .principles-title { position: absolute; left: 0; width: 1200px; top: 80px; text-align: center; font-size: 37px; font-weight: 700; font-style: italic; line-height: 50px; color: var(--ink); }
  .side-note { position: absolute; font-family: "Kanit", sans-serif; font-style: italic; font-weight: 600; font-size: 16px; line-height: 30px; text-transform: uppercase; }
  .side-note.left { left: 88px; top: 282px; }
  .side-note.right { left: 834px; top: 300px; }
  .wheel { position: absolute; left: 331px; top: 232px; width: 540px; height: 540px; }
  .closing-quote { position: absolute; left: 0; width: 1200px; top: 820px; text-align: center; font-family: "Kanit", sans-serif; font-style: italic; font-weight: 600; font-size: 20px; line-height: 31px; text-transform: uppercase; }

  /* Rules */
  .rules { position: absolute; left: 0; top: 2057px; width: 1200px; height: 750px; background: var(--charcoal-deep); }
  .rules-portrait { position: absolute; left: 68px; top: 91px; width: 369px; height: 520px; background: linear-gradient(160deg, #f4f4f4 0%, #d8d8d8 55%, #bdbdbd 100%); }
  .rules-title { position: absolute; left: 477px; top: 86px; color: var(--white); font-size: 36px; font-weight: 700; font-style: italic; line-height: 51px; }
  .rule-list { position: absolute; left: 480px; top: 210px; list-style: none; }
  .rule { display: flex; align-items: center; height: 58.4px; }
  .rule-badge { width: 40px; height: 40px; border-radius: 50%; background: var(--red); border: 2px solid #b23a30; color: var(--white); display: flex; flex-direction: column; align-items: center; justify-content: center; font-family: "Kanit", sans-serif; line-height: 1; margin-right: 17px; }
  .rule-badge b { font-size: 17px; font-weight: 700; }
  .rule-badge small { font-size: 7px; font-weight: 600; }
  .rule-text { color: var(--white); font-family: "Kanit", sans-serif; font-weight: 600; font-size: 15px; text-transform: uppercase; white-space: nowrap; }

  /* FAQ + footer */
  .footer { position: absolute; left: 0; top: 3116px; width: 1200px; height: 552px; background: var(--black); }
  .faq-card { position: absolute; left: 120px; top: 2885px; width: 960px; height: 309px; background: var(--green); border-radius: 22px; text-align: center; color: var(--white); }
  .faq-title { margin-top: 38px; font-size: 37px; font-weight: 700; letter-spacing: 0.5px; }
  .faq-text { width: 840px; margin: 12px auto 0; font-size: 15px; line-height: 30px; }
  .faq-btn { position: absolute; left: 415px; top: 231px; width: 128px; height: 43px; font-size: 12px; }
  .footer-brand { position: absolute; left: 0; width: 1200px; top: 3316px; text-align: center; font-family: "Kanit", sans-serif; font-weight: 600; font-size: 34px; color: var(--green-bright); }
  .footer-links { position: absolute; left: 0; width: 1200px; top: 3452px; display: flex; justify-content: center; gap: 44px; font-size: 15px; color: var(--white); }
  .copyright { position: absolute; left: 0; width: 1200px; top: 3508px; text-align: center; font-size: 13px; color: var(--white); }
  .copyright a { color: var(--green-bright); text-decoration: underline; }
  .social { position: absolute; left: 501px; top: 3561px; display: flex; gap: 10px; }
  .social-dot { width: 42px; height: 42px; border-radius: 50%; background: var(--white); border: 3px solid var(--white); }
  .social-dot.primary { background: var(--red-button); }
</style>
</head>
<body>
<div class="page">

  <header class="hero">
    <div class="hero-scene" role="img" aria-label="Dim brick basement fight room with benches, a barred window and a light beam"></div>
    <div class="brand">ORDER VANTAGE</div>
    <div class="menu">MENU <span class="menu-icon"></span></div>
    <h1 class="hero-title display">How much can you know about<br>yourself if you've never<br>been in a fight?</h1>
    <a class="btn hero-btn">Get Started</a>
  </header>

  <section class="intro">
    <svg class="intro-curve" width="1200" height="468" viewBox="0 0 1200 468">
      <path d="M0 350 C 180 380, 260 470, 420 460" fill="none" stroke="#6a6a6a" stroke-width="1"/>
      <path d="M1020 0 C 1120 40, 1150 160, 1200 200" fill="none" stroke="#6a6a6a" stroke-width="1"/>
      <path d="M0 0 H 420 C 360 60, 240 40, 160 90 C 90 130, 40 110, 0 140 Z" fill="#444"/>
    </svg>
    <h2 class="intro-title display">Dorian built himself an army</h2>
    <p class="intro-sub display">Why was Dorian building an army?</p>
    <p class="intro-text">To introduce and apply the core principles of success to highschool aged Jia Jitsa competitors.<br>We strive to work smarter not just si they can achieve their tell potherid</p>
    <p class="intro-motto display">In Dorian we trust</p>
    <div class="intro-portrait" role="img" aria-label="Illustrated figure in a dark fur coat holding a cup, set in a round frame"></div>
  </section>

  <section class="principles">
    <h2 class="principles-title display">Success is it's own reward so we<br>celebrate preparation</h2>

    <p class="side-note left">Without pain<br>without sacrifice<br>we would have nothing</p>
    <svg style="position:absolute;left:288px;top:402px" width="50" height="36" viewBox="0 0 50 36">
      <path d="M46 30 C 30 30, 18 22, 8 8" fill="none" stroke="#111" stroke-width="2"/>
      <path d="M4 4 L 6 16 M4 4 L 15 8" stroke="#111" stroke-width="2" fill="none"/>
    </svg>

    <p class="side-note right">Success is it's own reward so<br>we celebrate preparation</p>
    <svg style="position:absolute;left:872px;top:388px" width="50" height="36" viewBox="0 0 50 36">
      <path d="M4 30 C 20 30, 32 22, 42 8" fill="none" stroke="#111" stroke-width="2"/>
      <path d="M46 4 L 44 16 M46 4 L 35 8" stroke="#111" stroke-width="2" fill="none"/>
    </svg>

    <svg class="wheel" viewBox="-270 -270 540 540">
      <defs>
        <path id="ring-top" d="M -232 0 A 232 232 0 1 1 232 0 A 232 232 0 1 1 -232 0"/>
        <path id="ring-bottom" d="M -232 0 A 232 232 0 0 0 232 0"/>
      </defs>
      <circle r="262" fill="var(--green)"/>
      <circle r="202" fill="var(--red)" stroke="#fff" stroke-width="2"/>
      <g stroke="#fff" stroke-width="2">
        <line x1="-48" y1="-67" x2="-116" y2="-165"/>
        <line x1="7" y1="-82" x2="18" y2="-201"/>
        <line x1="58" y1="-58" x2="143" y2="-143"/>
        <line x1="82" y1="-7" x2="201" y2="-18"/>
        <line x1="68" y1="48" x2="165" y2="116"/>
        <line x1="22" y1="80" x2="52" y2="195"/>
        <line x1="-35" y1="75" x2="-85" y2="183"/>
        <line x1="-75" y1="35" x2="-183" y2="85"/>
        <line x1="-80" y1="-22" x2="-195" y2="-52"/>
      </g>
      <g fill="#fff" font-family="Kanit, sans-serif" font-weight="600" font-size="14" text-anchor="middle">
        <text transform="translate(-36,-135) rotate(75)"><tspan x="0" dy="-4">HELP YOUNG</tspan><tspan x="0" dy="16">COMPETIONS</tspan></text>
        <text transform="translate(59,-127) rotate(-65)"><tspan x="0" dy="-4">PERSONALIZE</tspan><tspan x="0" dy="16">GOALS FOR EACH</tspan></text>
        <text transform="translate(127,-59) rotate(-25)"><tspan x="0" dy="-4">PRIVATES</tspan><tspan x="0" dy="16">CHALLENGES</tspan></text>
        <text transform="translate(135,36) rotate(15)" dy="5">DRILS SPARIY</text>
        <text transform="translate(80,115) rotate(55)"><tspan x="0" dy="-4">VIDEOS PAST</tspan><tspan x="0" dy="16">FIGHYS</tspan></text>
        <text transform="translate(-12,139) rotate(-85)"><tspan x="0" dy="-4">STRONG</tspan><tspan x="0" dy="16">CONDITION</tspan></text>
        <text transform="translate(-99,99) rotate(-45)" dy="5">NUTRITION</text>
        <text transform="translate(-139,12) rotate(-5)" dy="5">RECOVERY</text>
        <text transform="translate(-115,-80) rotate(35)"><tspan x="0" dy="-4">FUN TRIPS</tspan><tspan x="0" dy="16">OUTING</tspan></text>
      </g>
      <circle r="83" fill="#fff" stroke="#fff" stroke-width="2"/>
      <circle r="70" fill="#111" stroke="var(--green-bright)" stroke-width="5" role="img" aria-label="Burning smiley face emblem"/>
      <g fill="#fff" font-family="Kanit, sans-serif" font-weight="700" font-size="28" text-anchor="middle">
        <text dy="8"><textPath href="#ring-top" startOffset="6.9%">SPIRIT</textPath></text>
        <text dy="8"><textPath href="#ring-top" startOffset="38.9%">TECHINCAL MIND</textPath></text>
        <text dy="8"><textPath href="#ring-bottom" startOffset="52%">BODY</textPath></text>
      </g>
    </svg>

    <p class="closing-quote">When the fight was over nothing was solved but nothing<br>mattered we all felt saved</p>
  </section>

  <section class="rules">
    <div class="rules-portrait" role="img" aria-label="Pencil sketch portrait of a member"></div>
    <h2 class="rules-title display">I don't want to die without<br>any scars</h2>
    <ol class="rule-list">
      <li class="rule"><span class="rule-badge"><b>01</b><small>RULE</small></span><span class="rule-text">Do not talk about OV</span></li>
      <li class="rule"><span class="rule-badge"><b>02</b><small>RULE</small></span><span class="rule-text">Do nst talk about OV</span></li>
      <li class="rule"><span class="rule-badge"><b>03</b><small>RULE</small></span><span class="rule-text">You protect the repitation of past present and future OV athetes</span></li>
      <li class="rule"><span class="rule-badge"><b>04</b><small>RULE</small></span><span class="rule-text">You do not contest close matches or complain</span></li>
      <li class="rule"><span class="rule-badge"><b>05</b><small>RULE</small></span><span class="rule-text">You will serve as a bridge between kid&nbsp; adult b55 competiting</span></li>
      <li class="rule"><span class="rule-badge"><b>06</b><small>RULE</small></span><span class="rule-text">You will attend teammate matches and help them whenever possible</span></li>
      <li class="rule"><span class="rule-badge"><b>07</b><small>RULE</small></span><span class="rule-text">You will alway treat competitors with respect</span></li>
      <li class="rule"><span class="rule-badge"><b>08</b><small>RULE</small></span><span class="rule-text">If you are in then you have fo fight</span></li>
    </ol>
  </section>

  <footer class="footer"></footer>

  <section class="faq-card">
    <h2 class="faq-title display">Common Questions</h2>
    <p class="faq-text">Why the "G2"? This is the second generation of our club. We were founded in the early 2000's. by close of hard rock fans who banned group together to create more unique concert experiences. Many of Order Vantage's guay members are still fritals and some even sponsor some 62 men bes&nbsp; How does someone get invital? pale are accepting indications of interest from competitors born in 2001 &amp; 2008</p>
    <a class="btn faq-btn">View More</a>
  </section>

  <div class="footer-brand">ORDER VANTAGE</div>
  <nav class="footer-links">
    <span>Terms &amp; conditions</span>
    <span>Privacy Policy</span>
    <span>About Us</span>
    <span>Support</span>
  </nav>
  <p class="copyright">Copyright© 2023&nbsp; <a>Order Vantage</a>&nbsp; |&nbsp; All Rights Reserved</p>
  <div class="social" aria-label="Social links">
    <span class="social-dot primary" aria-label="Social link 1"></span>
    <span class="social-dot" aria-label="Social link 2"></span>
    <span class="social-dot" aria-label="Social link 3"></span>
    <span class="social-dot" aria-label="Social link 4"></span>
  </div>

</div>
</body>
</html>
```